Ridgeline Haul Carriers - Website

A clean, not cluttered informative website for our business. We specialize in the transportation of radioactive materials across North America. The site is mostly for information about our company and will not be used to attract business but will be used to attract employee's mainly drivers. Driver's are very hard to find in our area. One of the pages needs to be a job's posting page with an apply now button. Either an application can be filled out there or a resume can be uploaded which ever functionality works better. I would like a website that I can easily edit, ability to change text and photos.

Number of Pages Required

5+ page

Colors

Designer to choose colors to be used in the design.

Requirements
Must have
• Home - About - Services - Jobs - Contact pages
• A way prospective employee's can apply or upload their resume to be emailed to me
• Very clean apperance
Should not have
• I don't want it to be busy

```html
<!DOCTYPE html>
<html lang="en">
<head>
<meta charset="utf-8">
<title>Ridgeline Haul Carriers</title>
<link href="https://fonts.googleapis.com/css2?family=Michroma&family=Montserrat:wght@400;600;700&family=Open+Sans:wght@400;600;700&display=swap" rel="stylesheet">
<style>
:root{
  --frame:#e6e7e8;
  --white:#ffffff;
  --blue:#1f73ba;
  --blue-band:#2f7fc0;
  --blue-deep:#1a5f9c;
  --ink:#1d2533;
  --body:#2c2f36;
  --field:rgba(20,45,80,.55);
}
*{box-sizing:border-box;margin:0;padding:0}
html,body{width:1200px;height:3285px;overflow:hidden;background:var(--frame)}
body{font-family:"Montserrat",sans-serif;color:var(--body)}
.page{position:absolute;left:17px;top:0;width:1166px;height:3268px;background:var(--white)}

/* hero */
.hero{position:absolute;left:0;top:0;width:1166px;height:723px;
  background:linear-gradient(180deg,#c9d3dc 0%,#9fb0c0 35%,#6f8294 60%,#d9dde2 85%,#ffffff 100%)}
.brand{position:absolute;left:23px;top:60px;font-family:"Michroma",sans-serif;font-size:24px;color:var(--blue);letter-spacing:1px;line-height:1.15}
.nav{position:absolute;left:610px;top:72px;display:flex;gap:38px;list-style:none}
.nav a{font-family:"Michroma",sans-serif;font-size:14px;color:var(--ink);text-decoration:none;text-transform:uppercase}
.nav a.active{color:var(--blue);border-bottom:2px solid var(--blue);padding-bottom:3px}
.hero-title{position:absolute;left:0;top:248px;width:1166px;text-align:center;font-family:"Montserrat",sans-serif;font-weight:700;font-size:33px;line-height:42px;color:var(--white);text-transform:uppercase;text-shadow:0 2px 6px rgba(0,0,0,.45)}

/* shared */
.section-title{font-family:"Michroma",sans-serif;font-size:22px;color:var(--ink);text-transform:uppercase;letter-spacing:.5px}
.section-title .accent{color:var(--blue)}
.section-title.light{color:var(--white)}
.btn{display:flex;align-items:center;justify-content:center;border:3px solid var(--blue);border-radius:26px;font-family:"Open Sans",sans-serif;font-weight:700;font-size:19px;color:var(--blue);text-decoration:none;background:var(--white)}
.btn.ghost{border-color:var(--white);color:var(--white);background:transparent}

/* about */
.about{position:absolute;left:0;top:723px;width:1166px;height:411px;text-align:center}
.about .section-title{position:absolute;left:0;top:40px;width:100%}
.about p{position:absolute;left:90px;top:105px;width:986px;font-size:17px;line-height:29px;color:var(--body)}
.about .btn{position:absolute;left:465px;top:274px;width:236px;height:48px}

/* services */
.services{position:absolute;left:0;top:1134px;width:1166px;height:546px;
  background:linear-gradient(180deg,#3a86c4 0%,var(--blue-band) 55%,#2a78b8 100%)}
.services .section-title{position:absolute;left:0;top:110px;width:100%;text-align:center}
.services .lead{position:absolute;left:60px;top:180px;width:1046px;text-align:center;font-size:17px;line-height:30px;color:var(--white)}
.materials{position:absolute;left:0;top:268px;width:1166px;height:200px;list-style:none}
.material{position:absolute;width:240px;text-align:center;color:var(--white);font-weight:600;font-size:18px;line-height:24px}
.material svg{display:block;margin:0 auto 22px;width:108px;height:108px}

/* join */
.join{position:absolute;left:0;top:1680px;width:1166px;height:563px}
.join .section-title{position:absolute;left:75px;top:120px}
.join p{position:absolute;left:75px;top:170px;width:466px;font-size:17px;line-height:30px;color:var(--body)}
.join .btn{position:absolute;left:75px;top:425px;width:241px;height:46px}
.join .photo{position:absolute;left:581px;top:90px;width:510px;height:380px;
  background:linear-gradient(160deg,#cfd9e3 0%,#a9b8c6 40%,#5f7384 75%,#7d8a94 100%)}

/* contact */
.contact{position:absolute;left:0;top:2243px;width:1166px;height:575px;
  background:linear-gradient(180deg,#3583c3 0%,var(--blue-band) 50%,#2773b3 100%)}
.contact .section-title{position:absolute;left:0;top:105px;width:100%;text-align:center}
.contact .sub{position:absolute;left:0;top:180px;width:100%;text-align:center;font-family:"Open Sans",sans-serif;font-weight:700;font-size:14px;color:var(--white);text-transform:uppercase}
.field{position:absolute;background:var(--field);color:var(--white);font-family:"Open Sans",sans-serif;font-weight:600;font-size:15px;padding:10px 14px}
.contact .btn{position:absolute;left:463px;top:440px;width:240px;height:46px}

/* footer */
.footer{position:absolute;left:0;top:2818px;width:1166px;height:412px}
.footer .brand{left:0;top:62px;width:100%;text-align:center;font-size:28px}
.col{position:absolute;top:170px;font-family:"Open Sans",sans-serif}
.col h3{font-size:14px;font-weight:700;color:var(--blue);text-transform:uppercase;padding-bottom:10px;border-bottom:1px solid #d4d7db;margin-bottom:14px}
.col ul{list-style:none;font-size:13px;line-height:19px;color:var(--body)}
.contact-list li{display:flex;gap:8px;margin-bottom:14px;align-items:flex-start}
.contact-list svg{width:18px;height:18px;flex:none}
.social li{display:flex;align-items:center;gap:10px;margin-bottom:14px}
.social .dot{width:16px;height:16px;border-radius:50%;background:var(--blue-deep)}
.newsletter{display:flex;margin-top:4px}
.newsletter .input{width:165px;height:36px;border:1px solid var(--blue);font-size:12px;padding:10px 8px;color:var(--body);font-weight:600}
.newsletter .submit{width:93px;height:36px;background:var(--blue);color:var(--white);font-size:13px;font-weight:700;display:flex;align-items:center;justify-content:center}
.copyright{position:absolute;left:0;top:3230px;width:1166px;height:38px;background:var(--blue);color:var(--white);font-family:"Open Sans",sans-serif;font-weight:700;font-size:12px;display:flex;align-items:center;justify-content:center;text-transform:uppercase}
</style>
</head>
<body>
<div class="page">

  <header class="hero" role="img" aria-label="Photo of a truck hauling radioactive material drums in front of an industrial power plant">
    <div class="brand">RIDGELINE HAUL CARRIERS</div>
    <ul class="nav">
      <li><a class="active" href="#">Home</a></li>
      <li><a href="#">About</a></li>
      <li><a href="#">Services</a></li>
      <li><a href="#">Jobs</a></li>
      <li><a href="#">Contact</a></li>
    </ul>
    <h1 class="hero-title">The leader in the transportation of radioactive<br>materials across North America</h1>
  </header>

  <section class="about">
    <h2 class="section-title">About <span class="accent">Ridgeline Haul Carriers</span></h2>
    <p>Lorem ipsum dolor sit amet, consectetur adipiscing elit, sed do eiusmod tempor incididunt ut labore et dolore magna aliqua. Ut enim ad minim veniam, quis nostrud exercitation ullamco laboris nisi ut aliquip ex ea commodo consequat. Duis aute irure dolor in reprehenderit in voluptate velit esse cillum dolore eu fugiat nulla pariatur. Excepteur sint occaecat cupidatat non proident, sunt in culpa qui officia des erunt mollit anim id est laborum.</p>
    <a class="btn" href="#">Learn More</a>
  </section>

  <section class="services" role="img" aria-label="Blue tinted photo of transport trucks on a highway">
    <h2 class="section-title light">Our Services</h2>
    <p class="lead">We are here to manage your logistical needs from start to finish, and our extensive experience allows us to offer innovative, reliable, and safe front-end nuclear transportation solutions for the following materials:</p>
    <ul class="materials">
      <li class="material" style="left:138px;top:0">
        <svg viewBox="0 0 108 108"><circle cx="54" cy="54" r="52" fill="#fff"/><circle cx="54" cy="54" r="42" fill="#1f73ba"/><circle cx="54" cy="54" r="26" fill="#fff"/><circle cx="54" cy="54" r="5" fill="#1f73ba"/><path d="M54 54 L44 36 A21 21 0 0 1 64 36 Z M54 54 L75 54 A21 21 0 0 1 65 72 Z M54 54 L43 72 A21 21 0 0 1 33 54 Z" fill="#1f73ba"/><circle cx="54" cy="54" r="6" fill="#fff"/><circle cx="54" cy="54" r="4" fill="#1f73ba"/></svg>
        Uranium ore<br>concentrates
      </li>
      <li class="material" style="left:390px;top:0">
        <svg viewBox="0 0 108 108"><circle cx="54" cy="54" r="52" fill="#fff"/><circle cx="54" cy="54" r="42" fill="#1f73ba"/><rect x="38" y="30" width="32" height="48" rx="4" fill="#fff"/><rect x="38" y="40" width="32" height="3" fill="#1f73ba"/><rect x="38" y="65" width="32" height="3" fill="#1f73ba"/><circle cx="54" cy="54" r="7" fill="#1f73ba"/></svg>
        Natural and enriched<br>uranium hexafluoride
      </li>
      <li class="material" style="left:642px;top:0">
        <svg viewBox="0 0 108 108"><circle cx="54" cy="54" r="52" fill="#fff"/><circle cx="54" cy="54" r="42" fill="#1f73ba"/><path d="M42 30 h14 v12 l12 28 h-38 l12 -28 z" fill="#fff"/><rect x="62" y="40" width="10" height="30" rx="2" fill="#fff"/><rect x="34" y="72" width="42" height="4" fill="#fff"/></svg>
        Uranium trioxide
      </li>
      <li class="material" style="left:890px;top:0">
        <svg viewBox="0 0 108 108"><circle cx="54" cy="54" r="52" fill="#fff"/><circle cx="54" cy="54" r="42" fill="#1f73ba"/><path d="M44 32 C36 46 32 52 32 60 a12 12 0 0 0 24 0 C56 52 52 46 44 32 Z" fill="#fff"/><path d="M66 42 C59 54 56 59 56 66 a10 10 0 0 0 20 0 C76 59 73 54 66 42 Z" fill="#fff"/></svg>
        Fuel pellets<br>and bundles
      </li>
    </ul>
  </section>

  <section class="join">
    <h2 class="section-title">Join <span class="accent">Ridgeline</span> Team</h2>
    <p>Lorem ipsum dolor sit amet, consectetur adipis cing elit, sed do eiusmod tempor incididunt ut labore et dolore magna aliqua. Ut enim ad min im veniam, quis nostrud exercitation ullamco la boris nisi ut aliquip ex ea commodo consequat. Duis aute irure dolor in reprehenderit in volupta te velit esse cillum dolore eu fugiat nulla pariat ur excepteur sint occaecat cupi.</p>
    <a class="btn" href="#">Apply Now</a>
    <div class="photo" role="img" aria-label="Photo of a truck driver holding a tablet in front of a row of parked trucks"></div>
  </section>

  <section class="contact" role="img" aria-label="Blue tinted photo of radioactive material drums">
    <h2 class="section-title light">Contact Us</h2>
    <div class="sub">Let us know what you need</div>
    <div class="field" style="left:116px;top:227px;width:313px;height:44px">Your Name</div>
    <div class="field" style="left:445px;top:227px;width:313px;height:44px">Your Email</div>
    <div class="field" style="left:773px;top:227px;width:313px;height:44px">Your Subject</div>
    <div class="field" style="left:116px;top:287px;width:970px;height:131px">Message</div>
    <a class="btn ghost" href="#">Send Message</a>
  </section>

  <footer class="footer">
    <div class="brand">RIDGELINE HAUL CARRIERS</div>
    <div class="col" style="left:57px;width:110px">
      <h3>Quick Links</h3>
      <ul><li>Home</li><li>About</li><li>Services</li><li>Jobs</li><li>Contact</li></ul>
    </div>
    <div class="col" style="left:224px;width:165px">
      <h3>Transport Services</h3>
      <ul><li>Uranium ore concentrates</li><li>Uranium hexafluoride</li><li>Uranium trioxide</li><li>Fuel pellets and bundles</li></ul>
    </div>
    <div class="col" style="left:454px;width:180px">
      <h3>Contact</h3>
      <ul class="contact-list">
        <li><svg viewBox="0 0 18 18"><circle cx="9" cy="9" r="8" fill="none" stroke="#2c2f36" stroke-width="1.4"/><path d="M9 4a3 3 0 0 0-3 3c0 2.2 3 6 3 6s3-3.8 3-6a3 3 0 0 0-3-3z" fill="#2c2f36"/></svg><span>Ridgeline Haul Carriers<br>48 Quarry Lane<br>Milton Ridge, NY 10001</span></li>
        <li><svg viewBox="0 0 18 18"><circle cx="9" cy="9" r="8" fill="none" stroke="#2c2f36" stroke-width="1.4"/><path d="M6 5l2 0 1 2.5-1.2 1a5 5 0 0 0 2.7 2.7l1-1.2 2.5 1v2a1 1 0 0 1-1 1A8 8 0 0 1 5 6a1 1 0 0 1 1-1z" fill="#2c2f36"/></svg><span>1800.555.0142</span></li>
        <li><svg viewBox="0 0 18 18"><circle cx="9" cy="9" r="8" fill="none" stroke="#2c2f36" stroke-width="1.4"/><rect x="5" y="6" width="8" height="6" fill="none" stroke="#2c2f36" stroke-width="1.2"/><path d="M5 6l4 3 4-3" fill="none" stroke="#2c2f36" stroke-width="1.2"/></svg><span>info@ridgelinehaul.com</span></li>
      </ul>
    </div>
    <div class="col" style="left:690px;width:100px">
      <h3>Follow Us</h3>
      <ul class="social"><li><span class="dot"></span>friendbook</li><li><span class="dot"></span>chirper</li><li><span class="dot"></span>snapgram</li></ul>
    </div>
    <div class="col" style="left:855px;width:260px">
      <h3>Newsletter</h3>
      <div class="newsletter"><div class="input">Enter Email Address</div><div class="submit">SIGN UP</div></div>
    </div>
  </footer>

  <div class="copyright">Copyright © 2019 Ridgeline Haul Carriers. All rights reserved.</div>
</div>
</body>
</html>
```